we can communicate on this, but i want to follow the approach we took on Pellew|Marsh & Quinlan but i feel the card front needs the black background and the platinum and gold logo. The back? I am open. we can use the same info from PM&Q. Velmont Arc is an enhanced equity investment fund - basically a very exclusive boutique hedge fund that uses only stock options. very advanced things. hope you are interested

Contact Information for Business Card

Dr. Lewis T. Brennick, CFA
Scientifique de fusée financière
701.555.0143
LTBquant47@mailvantor.com

4718 Willow Creek Bend W.
West Fargo, ND 58078

No web site

Colors

Designer to choose colors to be used in the design.

Requirements
Nice to have
• I tend to prefer the most visible applications of the logo to include logo and name, the logo version with a black background and the gold and platinum components separated by the black. I see this working well for a single side (logo and name - this is card front to me).
• I am fairly open to other treatments on the reverse side with the data. To me, it makes sense to have a different color rendition of the logo on the reverse and it may be a muted black tone on tone or an oversized portion that would have spot UV. Or, the reverse may play with colors and layout
Should not have
• Other colors = no no
• Decorative font

```html
<!DOCTYPE html>
<html lang="en">
<head>
<meta charset="utf-8">
<title>Velmont Arc — Business Card</title>
<link href="https://fonts.googleapis.com/css2?family=Montserrat:wght@700&family=Fira+Sans+Condensed:wght@600&family=Roboto:wght@400&display=swap" rel="stylesheet">
<style>
  :root {
    --backdrop: #3a3a3a;
    --card-black: #222224;
    --white: #ffffff;
    --gold: #c9a227;
    --gold-light: #e6cf5a;
    --gold-deep: #a8841a;
    --platinum-light: #d8d8dc;
    --platinum-dark: #6b6b70;
    --ink: #1c1c1c;
  }
  * { margin: 0; padding: 0; box-sizing: border-box; }
  html, body { width: 799px; height: 1200px; overflow: hidden; }
  body {
    background: var(--backdrop);
    position: relative;
    font-family: "Roboto", sans-serif;
  }
  .card {
    position: absolute;
    left: 50px;
    width: 700px;
    height: 400px;
    background: var(--card-black);
    overflow: hidden;
    box-shadow: 0 10px 30px rgba(0,0,0,0.45);
  }
  .card-front { top: 120px; }
  .card-back { top: 680px; }

  .brand-dot {
    border-radius: 50%;
    background: var(--gold);
    flex: none;
  }
  .brand-name {
    font-family: "Montserrat", sans-serif;
    font-weight: 700;
    color: var(--white);
    letter-spacing: 1px;
    white-space: nowrap;
  }

  .card-front .brand {
    position: absolute;
    inset: 0;
    display: flex;
    flex-direction: column;
    align-items: center;
    justify-content: center;
    gap: 18px;
  }
  .card-front .brand-dot { width: 120px; height: 120px; margin-left: 150px; }
  .card-front .brand-name { font-size: 56px; }

  .card-back .brand {
    position: absolute;
    left: 40px;
    top: 40px;
    display: flex;
    align-items: center;
    gap: 22px;
  }
  .card-back .brand-dot { width: 84px; height: 84px; }
  .card-back .brand-name { font-size: 44px; }

  .holder {
    position: absolute;
    left: 40px;
    top: 200px;
  }
  .holder-name {
    font-family: "Fira Sans Condensed", sans-serif;
    font-weight: 600;
    font-size: 22px;
    color: var(--gold);
    white-space: nowrap;
  }
  .holder-title {
    font-size: 15px;
    color: var(--white);
    margin-top: 2px;
    white-space: nowrap;
  }

  .rule-platinum {
    position: absolute;
    left: 0;
    top: 272px;
    width: 330px;
    height: 12px;
    background: linear-gradient(90deg, var(--platinum-light), var(--platinum-dark));
  }

  .contact {
    position: absolute;
    left: 410px;
    top: 190px;
    color: var(--white);
    font-size: 15px;
    line-height: 22px;
    list-style: none;
  }
  .contact li { display: flex; align-items: center; gap: 10px; white-space: nowrap; }
  .contact svg { width: 14px; height: 14px; flex: none; fill: var(--gold); }

  .band-gold {
    position: absolute;
    left: 330px;
    top: 330px;
    width: 370px;
    height: 70px;
    border-top-left-radius: 22px;
    background: linear-gradient(90deg, var(--gold-deep), var(--gold-light) 55%, var(--gold));
    display: flex;
    align-items: center;
    padding-left: 50px;
  }
  .band-gold .tagline {
    font-size: 17px;
    color: var(--ink);
    white-space: nowrap;
  }
</style>
</head>
<body>

  <section class="card card-front" aria-label="Card front">
    <div class="brand">
      <span class="brand-dot"></span>
      <span class="brand-name">VELMONT ARC</span>
    </div>
  </section>

  <section class="card card-back" aria-label="Card back">
    <div class="brand">
      <span class="brand-dot"></span>
      <span class="brand-name">VELMONT ARC</span>
    </div>

    <div class="holder">
      <p class="holder-name">Dr. Lewis T. Brennick, CFA</p>
      <p class="holder-title">Scientifique de fusée financière</p>
    </div>

    <div class="rule-platinum"></div>

    <ul class="contact">
      <li>
        <svg viewBox="0 0 24 24" aria-hidden="true"><path d="M6.6 10.8a15 15 0 0 0 6.6 6.6l2.2-2.2a1 1 0 0 1 1-.25 11.4 11.4 0 0 0 3.6.57 1 1 0 0 1 1 1V20a1 1 0 0 1-1 1A17 17 0 0 1 3 4a1 1 0 0 1 1-1h3.5a1 1 0 0 1 1 1c0 1.25.2 2.45.57 3.6a1 1 0 0 1-.25 1z"/></svg>
        <span>701.555.0143</span>
      </li>
      <li>
        <svg viewBox="0 0 24 24" aria-hidden="true"><path d="M2 5h20v14H2z"/><path d="M2 5l10 8 10-8" fill="none" stroke="#222224" stroke-width="2"/></svg>
        <span>LTBquant47@mailvantor.com</span>
      </li>
      <li>4718 Willow Creek Bend W.,</li>
      <li>West Fargo, ND 58078</li>
    </ul>

    <div class="band-gold">
      <span class="tagline">Enhanced Equity Investment Fund</span>
    </div>
  </section>

</body>
</html>
```